Website for new crypto research organization

See brief (attached). This is a pretty basic website with only a handful of pages + ability to collect email addresses.

```html
<!DOCTYPE html>
<html lang="en">
<head>
<meta charset="utf-8">
<title>Vantor Research – Website Pages</title>
<link href="https://fonts.googleapis.com/css2?family=Kumbh+Sans:wght@400;500;600;700&display=swap" rel="stylesheet">
<style>
:root{
  --board:#169a93;
  --teal:#1a9a93;
  --ink:#1c1c1c;
  --muted:#444;
  --soft:#f3f3f3;
  --line:#d8e6e5;
  --blue:#1b8fc9;
  --white:#fff;
}
*{margin:0;padding:0;box-sizing:border-box}
html,body{width:750px;height:1200px;overflow:hidden;background:var(--board)}
body{font-family:"Kumbh Sans",sans-serif;color:var(--ink);position:relative}
.page{position:absolute;width:350px;background:var(--white);overflow:hidden}
.page > *{position:absolute}
.c{transform:translateY(-50%);white-space:nowrap}
.center{left:0;right:0;text-align:center}
.header{left:0;top:0;width:100%;height:21px;background:var(--white)}
.header.grey{height:25px;background:var(--soft)}
.logo{left:33px;font-size:10px;font-weight:600;color:var(--teal)}
.nav{font-size:4.5px;color:var(--ink)}
.nav.active{color:var(--teal)}
.hero{left:0;top:21px;width:100%;height:168px;
  background:linear-gradient(120deg,#8f8f8f 0%,#6f7b7a 30%,#7a5c42 50%,#8c8f96 70%,#a35f8e 85%,#4c7fae 100%)}
.hero-title{left:33px;font-size:21px;font-weight:700;color:var(--white);line-height:22px}
.hero-sub{left:33px;font-size:5px;color:var(--white);line-height:8.4px;white-space:normal;width:130px}
.arrow{width:15px;height:15px;border-radius:50%;background:rgba(255,255,255,.75);transform:translate(-50%,-50%)}
.h2{font-size:13px;font-weight:700}
.small{font-size:5px;color:var(--muted)}
.rule{height:1.5px;background:var(--teal)}
.feature{width:40px;height:40px;border-radius:50%;background:var(--teal);transform:translate(-50%,-50%)}
.feature-label{width:80px;font-size:7.5px;font-weight:600;text-align:center;line-height:9.6px;transform:translate(-50%,-50%)}
.news-band{left:0;top:354px;width:100%;height:127px;background:#f5f8f8;border-top:.5px solid var(--teal);border-bottom:.5px solid var(--teal)}
.news-box{left:112px;top:372px;width:143px;height:89px;border:2px solid var(--teal);background:var(--white)}
.news-mark{font-size:15px;font-weight:700;color:var(--teal)}
.news-title{font-size:9.5px;font-weight:700}
.email-input{left:129px;top:430px;width:72px;height:15px;border:.5px solid var(--blue);background:var(--white);font-size:3.5px;color:#777;padding-left:5px;line-height:14px}
.subscribe{left:201px;top:430px;width:40px;height:15px;background:var(--blue);color:var(--white);font-size:4.5px;font-weight:600;text-align:center;line-height:15px}
.footer-bg{left:0;width:100%;background:var(--soft)}
.foot-link{font-size:5px;transform:translate(-50%,-50%)}
.social{width:12px;height:12px;border-radius:50%;border:.5px solid #bbb;background:var(--white);transform:translate(-50%,-50%);display:flex;align-items:center;justify-content:center}
.copy{font-size:4.5px}
.page-title{font-size:12px;font-weight:500}
.photo{background:linear-gradient(160deg,#9fa4a8,#6f757b)}
.person-name{font-size:8px;font-weight:600;color:var(--teal)}
.person-role{font-size:4.5px}
.bio{font-size:4px;line-height:8.3px;color:#333}
.art{background:linear-gradient(120deg,#8f8f8f 0%,#77706a 35%,#7a5c42 55%,#a35f8e 80%,#4c7fae 100%)}
.section-title{font-size:12px;font-weight:600;color:var(--teal)}
.intro{font-size:4.5px;line-height:8px;color:#333;text-align:center}
.block-title{font-size:9px;font-weight:500}
.block-text{font-size:3.8px;line-height:7.5px;color:#333}
.graffiti{background:linear-gradient(135deg,#2f4fa0 0%,#5aa9b8 35%,#c2442a 60%,#d98a3c 80%,#6a7a90 100%)}
.careers-text{font-size:3.8px;line-height:7.9px;color:#333}
.contact-band{left:0;top:212px;width:100%;height:122px;background:var(--soft)}
.contact-mail{font-size:4.5px}
</style>
</head>
<body>

<!-- Home page -->
<section class="page home" style="left:16px;top:24px;height:564px">
  <div class="header"></div>
  <div class="logo c" style="top:10px">Vantor Research</div>
  <div class="nav active c" style="left:218px;top:10px">Home</div>
  <div class="nav c" style="left:243px;top:10px">Team</div>
  <div class="nav c" style="left:261px;top:10px">Research</div>
  <div class="nav c" style="left:292px;top:10px">Careers</div>

  <div class="hero" role="img" aria-label="Elephant breaking through a graffiti brick wall"></div>
  <div class="hero-title" style="top:82px">Vantor<br>Research</div>
  <div class="hero-sub" style="top:131px">A research-first asset management firm investing in cryptocurrencies and web3.</div>
  <div class="arrow" style="left:16px;top:108px"><svg width="15" height="15" viewBox="0 0 15 15"><path d="M8.5 5 6 7.5 8.5 10" fill="none" stroke="#333" stroke-width=".8"/></svg></div>
  <div class="arrow" style="left:333px;top:108px"><svg width="15" height="15" viewBox="0 0 15 15"><path d="M6.5 5 9 7.5 6.5 10" fill="none" stroke="#333" stroke-width=".8"/></svg></div>

  <div class="h2 c center" style="top:225px">Research-Driven Investing</div>
  <div class="small c center" style="top:240px">Thesis-driven investing with value-added research</div>
  <div class="rule" style="left:159px;top:250px;width:32px"></div>

  <div class="feature" style="left:78px;top:284px"><svg width="40" height="40" viewBox="0 0 40 40"><circle cx="20" cy="20" r="9" fill="none" stroke="#fff" stroke-width="1"/><circle cx="20" cy="20" r="4" fill="none" stroke="#fff" stroke-width="1"/></svg></div>
  <div class="feature" style="left:175px;top:284px"><svg width="40" height="40" viewBox="0 0 40 40"><circle cx="15" cy="16" r="3" fill="none" stroke="#fff" stroke-width=".9"/><circle cx="25" cy="16" r="3" fill="none" stroke="#fff" stroke-width=".9"/><path d="M10 27c1-5 9-5 10 0M20 27c1-5 9-5 10 0" fill="none" stroke="#fff" stroke-width=".9"/></svg></div>
  <div class="feature" style="left:273px;top:284px"><svg width="40" height="40" viewBox="0 0 40 40"><rect x="11" y="12" width="18" height="14" fill="none" stroke="#fff" stroke-width=".9"/><path d="M14 23v-3M18 23v-5M22 23v-4M26 23v-7" stroke="#fff" stroke-width=".9"/></svg></div>
  <div class="feature-label" style="left:78px;top:314px">Technical<br>Evaluation</div>
  <div class="feature-label" style="left:175px;top:314px">Community<br>Engagement</div>
  <div class="feature-label" style="left:273px;top:314px">On-chain<br>data analysis</div>

  <div class="news-band"></div>
  <div class="news-box"></div>
  <div class="news-mark c" style="left:112px;width:143px;text-align:center;top:390px">VR</div>
  <div class="news-title c" style="left:112px;width:143px;text-align:center;top:406px">Newsletter Subscribe</div>
  <div class="small c" style="left:112px;width:143px;text-align:center;top:417px">Get more details to signup</div>
  <div class="email-input">Type your email...</div>
  <div class="subscribe">Subscribe</div>

  <div class="foot-link" style="left:115px;top:510px">Home</div>
  <div class="foot-link" style="left:142px;top:510px">Team</div>
  <div class="foot-link" style="left:172px;top:510px">Research</div>
  <div class="foot-link" style="left:203px;top:510px">News</div>
  <div class="foot-link" style="left:233px;top:510px">Careers</div>
  <div class="social" style="left:159px;top:527px"></div>
  <div class="social" style="left:175px;top:527px"></div>
  <div class="social" style="left:191px;top:527px"><svg width="6" height="4" viewBox="0 0 6 4"><rect width="6" height="4" fill="#333"/><path d="M0 0 3 2 6 0" fill="none" stroke="#fff" stroke-width=".5"/></svg></div>
  <div class="copy c center" style="top:545px">© 2022 All Rights Reserved</div>
</section>

<!-- Team page -->
<section class="page team" style="left:384px;top:24px;height:569px">
  <div class="header grey"></div>
  <div class="logo c" style="top:12px">Vantor Research</div>
  <div class="nav c" style="left:225px;top:12px">Home</div>
  <div class="nav active c" style="left:249px;top:12px">Team</div>
  <div class="nav c" style="left:271px;top:12px">Research</div>
  <div class="nav c" style="left:302px;top:12px">Careers</div>

  <div class="page-title c center" style="top:54px">Team</div>

  <div class="photo" style="left:33px;top:72px;width:129px;height:117px" role="img" aria-label="Portrait of Marcus Ellery"></div>
  <div class="person-name c" style="left:188px;top:102px">Marcus Ellery</div>
  <div class="person-role c" style="left:188px;top:112px">Founder and CEO</div>
  <div class="bio" style="left:188px;top:122px;width:130px">Marcus has spent his career focused on technology. In school he learned the basics of programming and developed websites for Northwind Systems. Then he pivoted to finance, investing technology companies for 15 years as a research analyst at Halvern and Corvel Asset Management.</div>

  <div class="photo" style="left:188px;top:196px;width:129px;height:117px" role="img" aria-label="Portrait of Owen Hartley"></div>
  <div class="person-name c" style="left:36px;top:235px">Owen Hartley</div>
  <div class="person-role c" style="left:36px;top:245px">Research Director</div>
  <div class="bio" style="left:36px;top:254px;width:126px">Owen has extensive experience as an investor. At Brightmoor Capital, a multi-billion-dollar asset manager, Owen conducted in-depth fundamental research on software companies.</div>

  <div class="photo" style="left:33px;top:320px;width:129px;height:117px" role="img" aria-label="Portrait of Ravi Menon"></div>
  <div class="person-name c" style="left:188px;top:350px">Ravi Menon</div>
  <div class="person-role c" style="left:188px;top:360px">Risk Management Director</div>
  <div class="bio" style="left:188px;top:369px;width:128px">Ravi has both academic and professional experience building portfolios and risk management controls for both traditional financial assets as well as cryptocurrencies. He earned a MS in computational finance from Westbrook University and developed quantitative tools at Harbor Lane</div>

  <div class="footer-bg" style="top:474px;height:95px"></div>
  <div class="foot-link" style="left:115px;top:510px">Home</div>
  <div class="foot-link" style="left:142px;top:510px">Team</div>
  <div class="foot-link" style="left:172px;top:510px">Research</div>
  <div class="foot-link" style="left:203px;top:510px">News</div>
  <div class="foot-link" style="left:233px;top:510px">Careers</div>
  <div class="social" style="left:159px;top:527px"></div>
  <div class="social" style="left:175px;top:527px"></div>
  <div class="social" style="left:191px;top:527px"><svg width="6" height="4" viewBox="0 0 6 4"><rect width="6" height="4" fill="#333"/><path d="M0 0 3 2 6 0" fill="none" stroke="#fff" stroke-width=".5"/></svg></div>
  <div class="copy c center" style="top:545px">© 2022 All Rights Reserved</div>
</section>

<!-- Research page -->
<section class="page research" style="left:16px;top:606px;height:570px">
  <div class="header grey"></div>
  <div class="logo c" style="top:12px">Vantor Research</div>
  <div class="nav c" style="left:225px;top:12px">Home</div>
  <div class="nav c" style="left:249px;top:12px">Team</div>
  <div class="nav active c" style="left:271px;top:12px">Research</div>
  <div class="nav c" style="left:302px;top:12px">Careers</div>

  <div class="section-title c center" style="top:57px">Research-Driven Investing</div>
  <div class="intro" style="left:55px;top:68px;width:240px">Vantor has an in-depth research process born from years of Wall Street experience, but adapted to crypto markets. In each case we develop a core thesis and then prove it out with our investment framework.</div>

  <div class="art" style="left:33px;top:102px;width:136px;height:113px" role="img" aria-label="Elephant breaking through a graffiti brick wall"></div>
  <div class="block-title c" style="left:175px;top:145px">Technology Evaluation</div>
  <div class="block-text" style="left:175px;top:154px;width:136px">For each investment we always start with the technology. We evaluate documentation and use the product to determine what problems it solves, how well it works, and if the economics are sound.</div>

  <div class="art" style="left:181px;top:223px;width:136px;height:113px" role="img" aria-label="Elephant breaking through a graffiti brick wall"></div>
  <div class="block-title c" style="left:33px;top:262px">Community Engagement</div>
  <div class="block-text" style="left:33px;top:271px;width:134px">Developer and user communities are key constituencies that determine a project's success, and in web3 these groups are active and available on public forums. Vantor develops relationships with contributors, ecosystem partners, and users to understand the key drivers of our investment.</div>

  <div class="art" style="left:33px;top:344px;width:136px;height:114px" role="img" aria-label="Elephant breaking through a graffiti brick wall"></div>
  <div class="block-title c" style="left:175px;top:387px">On-chain data analysis</div>
  <div class="block-text" style="left:175px;top:396px;width:136px">Blockchains contain significant amounts of public data. We use this information to track user/developer adoption, changes in ownership, and other trading dynamics to inform our investment decisions.</div>

  <div class="footer-bg" style="top:484px;height:86px"></div>
  <div class="foot-link" style="left:115px;top:517px">Home</div>
  <div class="foot-link" style="left:142px;top:517px">Team</div>
  <div class="foot-link" style="left:172px;top:517px">Research</div>
  <div class="foot-link" style="left:203px;top:517px">News</div>
  <div class="foot-link" style="left:233px;top:517px">Careers</div>
  <div class="social" style="left:159px;top:534px"></div>
  <div class="social" style="left:175px;top:534px"></div>
  <div class="social" style="left:191px;top:534px"><svg width="6" height="4" viewBox="0 0 6 4"><rect width="6" height="4" fill="#333"/><path d="M0 0 3 2 6 0" fill="none" stroke="#fff" stroke-width=".5"/></svg></div>
  <div class="copy c center" style="top:552px">© 2022 All Rights Reserved</div>
</section>

<!-- Careers page -->
<section class="page careers" style="left:384px;top:606px;height:416px">
  <div class="header grey"></div>
  <div class="logo c" style="top:12px">Vantor Research</div>
  <div class="nav c" style="left:225px;top:12px">Home</div>
  <div class="nav c" style="left:249px;top:12px">Team</div>
  <div class="nav c" style="left:271px;top:12px">Research</div>
  <div class="nav active c" style="left:302px;top:12px">Careers</div>

  <div class="graffiti" style="left:33px;top:55px;width:125px;height:120px" role="img" aria-label="Colourful graffiti on a brick wall"></div>
  <div class="page-title c" style="left:176px;top:66px">Careers</div>
  <div class="person-role c" style="left:176px;top:79px">Community Manager</div>
  <div class="careers-text" style="left:176px;top:86px;width:132px">Vantor Research is a research-first asset management firm investing in cryptocurrencies and web3. We combine Wall Street and technology experience to deliver value to our investors as well as the communities we invest in.</div>
  <div class="careers-text" style="left:176px;top:121px;width:132px">We are looking for people to help us engage with developer and user communities. We aren't concerned about resumes but are looking for people with a passion for crypto and a proven ability to connect with relevant people and to find out answers. Must be comfortable on social media, Chatterly, Wiremsg, and other forums. Non US-based Anons/pseudo-anons welcome.</div>

  <div class="contact-band"></div>
  <div class="page-title c center" style="top:237px">Contact Us</div>
  <div class="intro" style="left:80px;top:247px;width:190px;font-size:4px">Lorem ipsum dolor sit amet, consectetur adipiscing elit, sed do eiusmod tempor incididunt ut labore et dolore magna aliqua. Ut enim ad</div>
  <div class="social" style="left:168px;top:275px"></div>
  <div class="social" style="left:183px;top:275px"></div>
  <div class="social" style="left:76px;top:301px"><svg width="6" height="4" viewBox="0 0 6 4"><rect width="6" height="4" fill="#333"/><path d="M0 0 3 2 6 0" fill="none" stroke="#fff" stroke-width=".5"/></svg></div>
  <div class="contact-mail c" style="left:87px;top:301px">info@vantorlab.com</div>
  <div class="social" style="left:156px;top:301px"><svg width="6" height="4" viewBox="0 0 6 4"><rect width="6" height="4" fill="#333"/><path d="M0 0 3 2 6 0" fill="none" stroke="#fff" stroke-width=".5"/></svg></div>
  <div class="contact-mail c" style="left:167px;top:301px">info@vantorlab.com</div>
  <div class="social" style="left:237px;top:301px"><svg width="6" height="4" viewBox="0 0 6 4"><rect width="6" height="4" fill="#333"/><path d="M0 0 3 2 6 0" fill="none" stroke="#fff" stroke-width=".5"/></svg></div>
  <div class="contact-mail c" style="left:248px;top:301px">info@vantor.io</div>

  <div class="foot-link" style="left:115px;top:363px">Home</div>
  <div class="foot-link" style="left:142px;top:363px">Team</div>
  <div class="foot-link" style="left:172px;top:363px">Research</div>
  <div class="foot-link" style="left:203px;top:363px">News</div>
  <div class="foot-link" style="left:233px;top:363px">Careers</div>
  <div class="social" style="left:159px;top:380px"></div>
  <div class="social" style="left:175px;top:380px"></div>
  <div class="social" style="left:191px;top:380px"><svg width="6" height="4" viewBox="0 0 6 4"><rect width="6" height="4" fill="#333"/><path d="M0 0 3 2 6 0" fill="none" stroke="#fff" stroke-width=".5"/></svg></div>
  <div class="copy c center" style="top:398px">© 2022 All Rights Reserved</div>
</section>

</body>
</html>
```